TA BRAMLEY BUSINESS CARD DESIGN PROJECT

We need to utilize our logo that was expertly created on PixelHarbor and now need to match this with a business card design.

```html
<!DOCTYPE html>
<html lang="en">
<head>
<meta charset="utf-8">
<title>TA BRAMLEY Business Card</title>
<link href="https://fonts.googleapis.com/css2?family=Montserrat:wght@400;700;800&display=swap" rel="stylesheet">
<style>
  :root {
    --brand-blue: #0f57a8;
    --card-white: #ffffff;
    --backdrop: #e4e4e2;
    --shadow: rgba(0, 0, 0, 0.18);
  }
  * { margin: 0; padding: 0; box-sizing: border-box; }
  html, body {
    width: 1200px; height: 801px; overflow: hidden;
    background: var(--backdrop);
    font-family: "Montserrat", sans-serif;
  }
  .card-set {
    position: absolute; inset: 0;
    display: flex; align-items: center; justify-content: center; gap: 40px;
  }
  .card {
    position: relative; width: 540px; height: 309px;
    background: var(--brand-blue); overflow: hidden;
    box-shadow: 0 10px 24px var(--shadow);
  }
  .card__swoosh { position: absolute; inset: 0; width: 100%; height: 100%; }
  .wordmark {
    display: flex; align-items: center; gap: 12px;
    font-weight: 800; letter-spacing: 0.08em; white-space: nowrap;
  }
  .wordmark__square { display: block; flex: none; }
  .card--front .wordmark {
    position: absolute; top: 62px; right: 40px;
    color: var(--brand-blue); font-size: 30px;
  }
  .card--front .wordmark__square { width: 22px; height: 22px; background: var(--brand-blue); }
  .contact {
    position: absolute; left: 34px; bottom: 26px;
    color: var(--card-white); font-size: 12px; line-height: 1.35;
  }
  .contact__name { font-weight: 700; font-size: 17px; letter-spacing: 0.03em; }
  .contact__role { margin-bottom: 10px; }
  .contact__address { margin-bottom: 10px; }
  .contact__line { display: flex; align-items: center; gap: 7px; }
  .contact__icon { width: 11px; height: 11px; fill: var(--card-white); flex: none; }
  .card--back { display: flex; align-items: center; justify-content: center; }
  .card--back .wordmark { color: var(--card-white); font-size: 44px; }
  .card--back .wordmark__square { width: 30px; height: 30px; background: var(--card-white); }
</style>
</head>
<body>
  <main class="card-set">
    <section class="card card--front" aria-label="Business card front">
      <svg class="card__swoosh" viewBox="0 0 540 309" aria-hidden="true">
        <path d="M70,0 H540 V236 Q360,150 70,0 Z" fill="var(--card-white)"/>
        <path d="M40,0 Q360,168 540,262" fill="none" stroke="var(--card-white)" stroke-width="2.5"/>
      </svg>
      <div class="wordmark"><span class="wordmark__square"></span>TA BRAMLEY</div>
      <div class="contact">
        <p class="contact__name">MARCUS HALE</p>
        <p class="contact__role">Managing Director</p>
        <p class="contact__address">Your address, City<br>State, Zip 1234</p>
        <p class="contact__line">
          <svg class="contact__icon" viewBox="0 0 12 12" aria-hidden="true"><path d="M2,1 L4.5,1 L5.5,3.5 L4,4.6 Q5,7 7.4,8 L8.5,6.5 L11,7.5 L11,10 Q6,11 2,6 Q1,3.5 2,1 Z"/></svg>
          123 456 789
        </p>
        <p class="contact__line">
          <svg class="contact__icon" viewBox="0 0 12 12" aria-hidden="true"><path d="M1,2.5 H11 V9.5 H1 Z M1.5,3 L6,6.5 L10.5,3" stroke="var(--brand-blue)" stroke-width="0.8"/></svg>
          info@tabramley.com
        </p>
        <p class="contact__line">
          <svg class="contact__icon" viewBox="0 0 12 12" aria-hidden="true"><circle cx="6" cy="6" r="5"/><path d="M1,6 H11 M6,1 Q3,6 6,11 M6,1 Q9,6 6,11" fill="none" stroke="var(--brand-blue)" stroke-width="0.7"/></svg>
          www.tabramley.com
        </p>
      </div>
    </section>
    <section class="card card--back" aria-label="Business card back">
      <div class="wordmark"><span class="wordmark__square"></span>TA BRAMLEY</div>
    </section>
  </main>
</body>
</html>
```